Email Preference Page Design

We are looking for a 2 page design for our users to edit their email preferences and submit friend referrals. You can find the fuctionality, content and text here:

https://brightvanta.mailrelayhub.example/app/linkClick/7281/5fa9c1d3b07e442b/28374615/9bd4e01a7c3f2a65

* the shipping and billing address might be different so you need to show the billing if the "same as shipping" box is not checked. It can auto-hide like the page above shows if that fits your design.

* when the "unsubscribe from all email lists" box is selected, all the other checkbox options will hide as in the example page. We need you to show us what the site will look like with and without that checkbox selected.

We want to match these two pages to the general feel of these website pages:

www.brightvanta.com
and
free.brightvanta.com

The page should be very clean and tight. Project is for design only but must be able to be implemented in html showing button and checkbox states. Technically this must be two pages for our system - one for all the user info and one for individual email referrals (see example above).

Target Market(s)

video professionals

Industry/Entity Type

Shipping

Requirements
Must have
• our logo (see numerous versions attached)
well designed header
well designed sections
clean editable text
tight layout
html friendly
easy to understand
2 pages
Nice to have
• custom checkboxes and radio buttons

```html
<!DOCTYPE html>
<html lang="en">
<head>
<meta charset="utf-8">
<title>Brightvanta – Communication Preferences</title>
<link rel="stylesheet" href="https://fonts.googleapis.com/css2?family=Exo+2:wght@400;500&family=Open+Sans:ital,wght@0,400;0,600;0,700;1,400&display=swap">
<style>
  :root {
    --orange: #f58634;
    --ink: #28333d;
    --text: #4a4f55;
    --label: #5b6066;
    --field-border: #d3d6d9;
    --field-focus-bg: #eef9fc;
    --field-focus-border: #8ab8c4;
    --white: #ffffff;
  }
  * { box-sizing: border-box; margin: 0; padding: 0; }
  html, body { width: 1200px; height: 2624px; overflow: hidden; }
  body {
    position: relative;
    background: var(--white);
    font-family: "Open Sans", Arial, sans-serif;
    color: var(--text);
  }

  /* Header */
  .top-bar { position: absolute; left: 0; top: 0; width: 1200px; height: 87px; background: var(--ink); }
  .brand-tab {
    position: absolute; left: 285px; top: 0; width: 630px; height: 166px;
    background: var(--white);
    border-radius: 0 0 40px 40px / 0 0 30px 30px;
    box-shadow: 0 6px 0 -2px #eceeef;
    display: flex; align-items: center; justify-content: center; gap: 18px;
    padding-bottom: 14px;
  }
  .brand-dot { width: 40px; height: 40px; border-radius: 50%; background: var(--orange); }
  .brand-name { font-weight: 600; font-size: 58px; color: var(--ink); letter-spacing: -0.5px; }
  .required-tag {
    position: absolute; left: 1015px; top: 87px; width: 185px; height: 39px;
    background: var(--orange); color: var(--white);
    font-size: 17px; line-height: 39px; text-align: center;
    clip-path: polygon(0 0, 100% 0, 100% 100%, 9% 100%);
    padding-left: 14px;
  }

  .page-title {
    position: absolute; left: 0; top: 222px; width: 1200px; text-align: center;
    font-family: "Exo 2", Arial, sans-serif; font-weight: 400; font-size: 70px; color: var(--ink);
  }

  /* Section headers */
  .section-head {
    position: absolute; height: 32px;
    font-size: 30px; font-weight: 600; color: var(--orange); line-height: 1;
    border-bottom: 3px solid var(--orange);
  }
  .section-head .caption { position: absolute; left: 0; bottom: 16px; white-space: nowrap; }
  .section-head::after {
    content: ""; position: absolute; left: 16px; bottom: -13px;
    border-left: 10px solid transparent; border-right: 10px solid transparent; border-top: 11px solid var(--orange);
  }
  .contact-head { left: 49px; top: 405px; width: 511px; }
  .shipping-head { left: 640px; top: 405px; width: 506px; }

  /* Form rows */
  .field-row { position: absolute; display: flex; align-items: center; height: 52px; }
  .field-label { font-size: 21px; color: var(--label); text-align: right; flex: none; }
  .field-box {
    flex: none; height: 52px; border: 2px solid var(--field-border); background: var(--white);
    font-size: 21px; color: var(--label); padding-left: 14px; display: flex; align-items: center; position: relative;
  }
  .field-box.is-focused { background: var(--field-focus-bg); border-color: var(--field-focus-border); }
  .field-box.is-select::before {
    content: ""; position: absolute; right: 42px; top: 0; bottom: 0; border-left: 2px solid var(--field-border);
  }
  .field-box.is-select::after {
    content: ""; position: absolute; right: 14px; top: 20px;
    border-left: 8px solid transparent; border-right: 8px solid transparent; border-top: 12px solid #9aa0a6;
  }
  .plus { flex: none; font-size: 20px; color: var(--label); text-align: center; }

  .contact-row { left: 0; }
  .contact-row .field-label { width: 201px; }
  .contact-row .field-box { margin-left: 12px; width: 347px; }
  .contact-row.postal .field-box.code { width: 140px; }
  .contact-row.postal .plus { width: 39px; }
  .contact-row.postal .field-box.ext { width: 168px; margin-left: 0; }

  .ship-row { left: 630px; }
  .ship-row .field-label { width: 175px; }
  .ship-row .field-box { margin-left: 10px; width: 332px; }
  .ship-row.postal .field-box.code { width: 129px; margin-left: 21px; }
  .ship-row.postal .plus { width: 38px; }
  .ship-row.postal .field-box.ext { width: 154px; margin-left: 0; }

  .same-address {
    position: absolute; left: 640px; top: 466px; width: 440px;
    display: flex; gap: 14px; font-size: 29px; line-height: 36px; color: var(--text);
  }
  .same-address .box { flex: none; width: 24px; height: 24px; border: 2px solid #b9bec3; background: var(--white); margin-top: 6px; }

  /* Orange preferences panel */
  .prefs-panel { position: absolute; left: 0; top: 1247px; width: 1200px; height: 1284px; background: var(--orange); }
  .panel-badge { position: absolute; left: 555px; top: 1202px; width: 90px; height: 90px; border-radius: 50%; background: var(--orange); }
  .on-orange { color: var(--white); }

  .check { flex: none; width: 24px; height: 24px; background: var(--white); border: 2px solid #e7e7e7; }
  .subscribe { position: absolute; left: 51px; top: 1372px; display: flex; gap: 13px; }
  .subscribe .check { margin-top: 4px; }
  .subscribe-title { font-size: 30px; font-weight: 700; line-height: 34px; }
  .subscribe-note { font-size: 27px; font-style: italic; line-height: 36px; }

  .filter-note { position: absolute; left: 49px; top: 1462px; font-size: 30px; font-weight: 700; white-space: nowrap; }

  .list-head {
    position: absolute; top: 1531px; width: 512px; height: 92px;
    border-top: 3px solid var(--white);
    border-bottom: 3px solid var(--white);
    font-size: 29px; font-weight: 600; line-height: 31px;
  }
  .list-head::after {
    content: ""; position: absolute; left: 16px; bottom: -13px;
    border-left: 10px solid transparent; border-right: 10px solid transparent; border-top: 11px solid var(--white);
  }
  .list-head.left { left: 51px; }
  .list-head.right { left: 633px; width: 513px; }
  .list-head span { position: absolute; left: 0; bottom: 12px; }

  .topic-list { position: absolute; list-style: none; display: flex; flex-direction: column; gap: 30.5px; }
  .topic-list li { display: flex; align-items: center; gap: 19px; font-size: 22px; line-height: 24px; white-space: nowrap; }
  .topic-list.left { left: 51px; top: 1662px; }
  .topic-list.right { left: 633px; top: 1662px; }

  .unsubscribe {
    position: absolute; left: 635px; top: 2090px; width: 509px; height: 65px;
    background: var(--white); border: 2px solid #d6d6d6;
    display: flex; align-items: center; gap: 14px; padding-left: 14px;
    font-size: 27px; font-weight: 700; color: var(--ink); white-space: nowrap;
  }
  .unsubscribe .check { border-color: #c2c6ca; }

  .submit-button {
    position: absolute; left: 51px; top: 2384px; width: 362px; height: 81px;
    background: var(--white); border: 3px solid #b96124;
    font-size: 38px; font-weight: 600; color: var(--ink);
    display: flex; align-items: center; justify-content: center;
  }

  .bottom-bar { position: absolute; left: 0; top: 2531px; width: 1200px; height: 93px; background: var(--ink); }
</style>
</head>
<body>

<header>
  <div class="top-bar"></div>
  <div class="brand-tab"><span class="brand-dot"></span><span class="brand-name">brightvanta</span></div>
  <div class="required-tag">Required Fields*</div>
</header>

<h1 class="page-title">Communication Preferences</h1>

<section class="contact-form">
  <h2 class="section-head contact-head"><span class="caption">Contact &amp; Billing</span></h2>
  <div class="field-row contact-row" style="top:470px"><span class="field-label">First Name*</span><span class="field-box is-focused"></span></div>
  <div class="field-row contact-row" style="top:530px"><span class="field-label">Last Name*</span><span class="field-box"></span></div>
  <div class="field-row contact-row" style="top:589px"><span class="field-label">Email *</span><span class="field-box"></span></div>
  <div class="field-row contact-row" style="top:649px"><span class="field-label">Phone</span><span class="field-box"></span></div>
  <div class="field-row contact-row" style="top:708px"><span class="field-label">Address 1</span><span class="field-box"></span></div>
  <div class="field-row contact-row" style="top:768px"><span class="field-label">Address 2</span><span class="field-box"></span></div>
  <div class="field-row contact-row" style="top:827px"><span class="field-label">Address 3</span><span class="field-box"></span></div>
  <div class="field-row contact-row" style="top:887px"><span class="field-label">City</span><span class="field-box"></span></div>
  <div class="field-row contact-row" style="top:950px"><span class="field-label">Select Country</span><span class="field-box is-select"></span></div>
  <div class="field-row contact-row" style="top:1007px"><span class="field-label">State</span><span class="field-box"></span></div>
  <div class="field-row contact-row postal" style="top:1076px"><span class="field-label">Postal Code + 4</span><span class="field-box code">11111</span><span class="plus">+</span><span class="field-box ext">1111</span></div>
</section>

<section class="shipping-form">
  <h2 class="section-head shipping-head"><span class="caption">Shipping Address</span></h2>
  <div class="same-address"><span class="box"></span><span>Billing address is same as shipping address</span></div>
  <div class="field-row ship-row" style="top:575px"><span class="field-label">Street Address 1</span><span class="field-box"></span></div>
  <div class="field-row ship-row" style="top:636px"><span class="field-label">Street Address 2</span><span class="field-box"></span></div>
  <div class="field-row ship-row" style="top:696px"><span class="field-label">Street Address 3</span><span class="field-box"></span></div>
  <div class="field-row ship-row" style="top:755px"><span class="field-label">City</span><span class="field-box"></span></div>
  <div class="field-row ship-row" style="top:818px"><span class="field-label">Select Country</span><span class="field-box is-select"></span></div>
  <div class="field-row ship-row" style="top:875px"><span class="field-label">State</span><span class="field-box"></span></div>
  <div class="field-row ship-row postal" style="top:935px"><span class="field-label">Postal Code + 4</span><span class="field-box code">44444</span><span class="plus">+</span><span class="field-box ext">2222</span></div>
</section>

<div class="prefs-panel"></div>
<div class="panel-badge"></div>

<div class="subscribe on-orange">
  <span class="check"></span>
  <div>
    <p class="subscribe-title">Subscribe me to your general email list</p>
    <p class="subscribe-note">This monthly email includes free video loops and VIP sale notices</p>
  </div>
</div>

<p class="filter-note on-orange">Help us filter our emails so we only sending relevant information to you</p>

<h3 class="list-head left on-orange"><span>Send me emails about these<br>product types:</span></h3>
<h3 class="list-head right on-orange"><span>Send me emails about these<br>product types:</span></h3>

<ul class="topic-list left on-orange">
  <li><span class="check"></span>Low energy motion loops</li>
  <li><span class="check"></span>High energy motion loops</li>
  <li><span class="check"></span>Timelapse footage</li>
  <li><span class="check"></span>Low energy motion loops</li>
  <li><span class="check"></span>High energy motion loops</li>
  <li><span class="check"></span>Timelapse footage</li>
  <li><span class="check"></span>Worship or wedding motion loops</li>
  <li><span class="check"></span>Pre-mixed DVDs and BluRay</li>
  <li><span class="check"></span>Entertainment lasers for concerts and clubs</li>
  <li><span class="check"></span>Entertainment lasers for text &amp; logo display</li>
  <li><span class="check"></span>Custom logo animation services</li>
  <li><span class="check"></span>Video software for creating video animations</li>
  <li><span class="check"></span>Video software for live performance (Vjing)</li>
</ul>

<ul class="topic-list right on-orange">
  <li><span class="check"></span>Vjing (live performance video)</li>
  <li><span class="check"></span>DJing (live performance audio+video)</li>
  <li><span class="check"></span>Performing in a band</li>
  <li><span class="check"></span>Video editing</li>
  <li><span class="check"></span>Corporate presentations</li>
  <li><span class="check"></span>Worship video services</li>
  <li><span class="check"></span>Lasers for entertainment &amp; branding</li>
  <li><span class="check"></span>Special offers from BrightVanta partners</li>
</ul>

<div class="unsubscribe"><span class="check"></span>Unsubscribe from all email lists</div>

<div class="submit-button">Submit Now</div>

<footer class="bottom-bar"></footer>

</body>
</html>
```